Standardization and redesign of graphics for a non-fiction book

For a book project, 11 graphics need to be visually unified so that all the graphics in the book are in the same style. The graphics must be created from scratch. Just new colors aren't enough. Some of the existing graphics are by other authors who own the copyright. Accordingly, the new graphics must be truly new. This is especially true for the "2 S-curves" graphic.

Target Market(s)

Manager Furniture Industry

Industry/Entity Type

Möbel

Colors
0054AA
0677BA
7BADD7
CADEEF
E8F1F8

```html
<!DOCTYPE html>
<html lang="de">
<head>
<meta charset="utf-8">
<title>Geschäftsmodell rund um den Zielkunden</title>
<link rel="stylesheet" href="https://fonts.googleapis.com/css2?family=Poppins:wght@400;500;600;700&display=swap">
<style>
  :root {
    --teal: #1fe0c8;
    --blue: #1560bd;
    --ink: #3a4563;
    --ring: #3a4660;
    --paper: #ffffff;
    --core-light: #fafafc;
    --core-dark: #e6e6ec;
  }
  * { margin: 0; padding: 0; box-sizing: border-box; }
  html, body { width: 1200px; height: 1200px; overflow: hidden; background: var(--paper); }
  body { font-family: "Poppins", sans-serif; position: relative; }

  .header-band {
    position: absolute; left: 390px; top: 0; width: 420px; height: 34px;
    background: var(--teal);
  }
  .ring { position: absolute; left: 0; top: 0; width: 1200px; height: 1200px; }

  .core {
    position: absolute; left: 438px; top: 448px; width: 296px; height: 296px;
    border-radius: 50%;
    background: linear-gradient(225deg, var(--core-dark), var(--core-light) 75%);
    border: 4px solid #ececee;
    box-shadow: 0 6px 18px rgba(0,0,0,0.06);
    display: flex; align-items: center; justify-content: center;
  }
  .core-title { font-size: 34px; font-weight: 700; color: var(--ink); }

  .segment {
    position: absolute; width: 216px; height: 216px; border-radius: 50%;
    display: flex; flex-direction: column; align-items: center; justify-content: center;
    text-align: center; padding: 0 14px;
  }
  .segment--teal { background: var(--teal); color: var(--ink); }
  .segment--blue { background: var(--blue); color: #fff; }
  .segment-title { font-size: 14.5px; font-weight: 700; margin-bottom: 6px; }
  .segment-text { font-size: 11px; line-height: 1.42; font-weight: 400; }
  .segment-text--large { font-size: 15px; line-height: 1.35; }
  .segment-text--small { font-size: 10.5px; line-height: 1.38; }
  .segment-text--dark { color: #111; }

  .leistung      { left: 478px; top: 194px; }
  .kanaele       { left: 729px; top: 321px; }
  .wertschoepf   { left: 729px; top: 619px; }
  .wertverteil   { left: 478px; top: 782px; }
  .ertrag        { left: 228px; top: 619px; }
  .entwicklung   { left: 228px; top: 321px; }
</style>
</head>
<body>
  <div class="header-band"></div>

  <svg class="ring" viewBox="0 0 1200 1200" aria-hidden="true">
    <circle cx="586" cy="596" r="308" fill="none" stroke="var(--ring)" stroke-width="4"/>
  </svg>

  <div class="core"><span class="core-title">Zielkunde</span></div>

  <div class="segment segment--teal leistung">
    <div class="segment-title">Leistungskonzept</div>
    <div class="segment-text">Angebotspalette:<br><br>Wohnungseinrichtungsgegenst ände und damit verbundenen Dienstleistungen wie Beratung, Lieferung, Entsorgung, Reparatur, Ersatzteile, …</div>
  </div>

  <div class="segment segment--blue kanaele">
    <div class="segment-title">Kanäle</div>
    <div class="segment-text segment-text--large">Kommunikations- und Verkaufskanäle (Single-, Multiple- und Omni-Channel)POS-Konzept</div>
  </div>

  <div class="segment segment--teal wertschoepf">
    <div class="segment-title">Wertschöpfungskonzept</div>
    <div class="segment-text segment-text--small">vertikale Integration vs reiner Handel, Einkaufsstrategie (Global- oder Local-Sourcing, Lagerhaltung, Einzelstückfertigung, …)Innenarchitektur, komplexe Einrichtungsberatung, Farb- und Stylingkonzepte, …</div>
  </div>

  <div class="segment segment--blue wertverteil">
    <div class="segment-title">Wertverteilung</div>
    <div class="segment-text">Shareholder-Konzept, Einbezug des Managements und der Mitarbeiter, Öffentlichkeitsinteresse</div>
  </div>

  <div class="segment segment--teal ertrag">
    <div class="segment-title">Ertragsmodell</div>
    <div class="segment-text segment-text--dark">margengetriebenes Modell (Verkaufspreise), Miete, Dienstleistungsgebühren (Living as a Service, Logistik, Reparatur)</div>
  </div>

  <div class="segment segment--blue entwicklung">
    <div class="segment-title">Entwicklungskonzept</div>
    <div class="segment-text">z.B. Open Innovation im Rahmen eines 2-S-Kurven-ModellsService- &amp; ProduktentwicklungDigitalstr ategie, Nachhaltigkeitsstrategie</div>
  </div>
</body>
</html>
```